COVID-19 Accredited CME Impact Infographic

We want an infographic showing how much COVID-19 Continuing Medical Education we have accredited and its impact. Our website is at https://med.kelbrook.edu/cme/COVID19/education.html The attached document is intended to simply show the elements. You have complete freedom on design. We will be updating the numbers weekly so it is important that we have the files so that we can update it. This can be done in powerpoint, publisher, word, in-design, illustrator. Don't use crazy fonts that we wont have.

Target Market(s)

Internal to Kelbrook. We just want to show the impact of our work

Industry/Entity Type

Education

Requirements
Must have
• We must be able to update the numbers ourselves.

See attached document for the pieces that we want.

The sizes of the numbers in the attached are based on importance to us.
Nice to have
• Not mandatory but try to use these colors. https://med.kelbrook.edu/identity/color-palette.html

I was thinking that perhaps the big number could be done in traditional train. Like this: https://www.pixelvarda.com/image-illustration/flip-board-under-constuction-page-isolated-4816203957

```html
<!DOCTYPE html>
<html lang="en">
<head>
<meta charset="utf-8">
<title>COVID-19 CME Impact – Kelbrook Medicine</title>
<link rel="stylesheet" href="https://fonts.googleapis.com/css2?family=Anton&family=Jost:wght@300;400&display=swap">
<style>
  :root {
    --bg-top: #a5bbc4;
    --bg-bottom: #ffffff;
    --title-grey: #3c4850;
    --title-navy: #042c45;
    --brand-red: #8c1515;
    --label-bg: #454e53;
    --label-text: #eef2f3;
    --tile-light: #a8bec7;
    --tile-light-low: #a3b9c2;
    --tile-light-edge: #dcecf2;
    --tile-light-rim: #4f5b61;
    --digit-dark: #042c45;
    --tile-dark-top: #0d4764;
    --tile-dark-hi: #1a6585;
    --tile-dark-low: #083d5a;
    --tile-dark-edge: #7cc0da;
    --tile-dark-rim: #05233a;
    --digit-light: #ffffff;
    --shadow: rgba(45, 66, 80, 0.34);
  }
  * { box-sizing: border-box; margin: 0; padding: 0; }
  html, body { width: 1200px; height: 1148px; overflow: hidden; }
  body {
    position: relative;
    background: linear-gradient(to bottom, var(--bg-top) 0%, #c9d5db 50%, var(--bg-bottom) 96%);
    font-family: "Jost", "Century Gothic", sans-serif;
  }

  .headline {
    position: absolute; left: 94px; top: 124px;
    font-family: "Anton", "Impact", sans-serif;
    font-size: 104px; line-height: 1; letter-spacing: 0.5px;
    color: var(--title-grey);
    transform: scaleX(1.12); transform-origin: left center;
  }
  .headline .headline-accent { color: var(--title-navy); }

  .brand {
    position: absolute; right: 80px; top: 150px;
    display: flex; align-items: center; gap: 14px;
    font-family: "Jost", sans-serif; font-weight: 400;
    font-size: 42px; line-height: 1; color: var(--brand-red);
  }
  .brand-mark { width: 40px; height: 40px; background: var(--brand-red); }

  .stat { position: absolute; }
  .stat-label {
    display: block; height: 31px; padding-left: 22px;
    background: var(--label-bg); border-radius: 6px;
    color: var(--label-text); font-size: 20px; font-weight: 400;
    line-height: 32px; text-transform: uppercase; letter-spacing: 0.2px;
    margin-bottom: 14px;
  }
  .board { display: flex; gap: 15px; }
  .board .pair-break { margin-left: 26px; }
  .board--wide { gap: 17px; }

  .tile {
    position: relative; width: 96px; height: 160px;
    border-radius: 6px; text-align: center;
    font-size: 126px; font-weight: 300; line-height: 158px;
  }
  .tile::before {
    content: ""; position: absolute; left: 0; top: 0;
    width: 186px; height: 250px; z-index: -1;
    clip-path: polygon(96px 0, 186px 90px, 186px 250px, 90px 250px, 0 160px, 0 0);
    background: linear-gradient(135deg, var(--shadow) 30%, rgba(45, 66, 80, 0) 78%);
  }
  .tile::after {
    content: ""; position: absolute; left: 0; right: 0; top: 78px; height: 4px;
    border-radius: 2px;
  }
  .tile--light {
    color: var(--digit-dark);
    background: linear-gradient(to bottom, var(--tile-light) 0 50%, var(--tile-light-low) 50% 100%);
    border: 2px solid var(--tile-light-rim);
    border-top-color: var(--tile-light-edge);
  }
  .tile--light::after { background: rgba(90, 108, 116, 0.55); }
  .tile--dark {
    color: var(--digit-light);
    background: linear-gradient(to bottom, var(--tile-dark-top) 0%, var(--tile-dark-hi) 48%, var(--tile-dark-low) 50%, var(--tile-dark-low) 100%);
    border: 2px solid var(--tile-dark-rim);
    border-top-color: var(--tile-dark-edge);
  }
  .tile--dark::after { background: var(--tile-dark-edge); opacity: 0.8; }

  .stat--states     { left: 93px;  top: 267px; }
  .stat--countries  { left: 345px; top: 267px; }
  .stat--activities { left: 674px; top: 267px; }
  .stat--cme        { left: 93px;  top: 533px; }
  .stat--live       { left: 674px; top: 533px; }
  .stat--views      { left: 93px;  top: 790px; }

  .stat--states .stat-label, .stat--countries .stat-label, .stat--activities .stat-label { width: 173px; }
  .stat--cme .stat-label, .stat--live .stat-label { width: 205px; }
  .stat--views .stat-label { width: 363px; }
  .stat--activities .board .pair-break, .stat--live .board .pair-break { margin-left: 33px; }
  .stat--cme .board .pair-break { margin-left: 26px; }
  .stat--cme .stat-label, .stat--live .stat-label, .stat--views .stat-label { margin-bottom: 18px; }
</style>
</head>
<body>
  <h1 class="headline">COVID-19<span class="headline-accent">CME</span></h1>

  <div class="brand">
    <span class="brand-mark" aria-hidden="true"></span>
    <span class="brand-name">Kelbrook Medicine</span>
  </div>

  <section class="stat stat--states">
    <span class="stat-label">Of States</span>
    <div class="board">
      <span class="tile tile--light">2</span>
      <span class="tile tile--light">6</span>
    </div>
  </section>

  <section class="stat stat--countries">
    <span class="stat-label">Of Countries</span>
    <div class="board">
      <span class="tile tile--light">1</span>
      <span class="tile tile--light">2</span>
    </div>
  </section>

  <section class="stat stat--activities">
    <span class="stat-label">Of Activities</span>
    <div class="board">
      <span class="tile tile--dark">2</span>
      <span class="tile tile--dark">3</span>
      <span class="tile tile--light pair-break"></span>
      <span class="tile tile--light"></span>
    </div>
  </section>

  <section class="stat stat--cme">
    <span class="stat-label">Of CME Learners</span>
    <div class="board">
      <span class="tile tile--light">5</span>
      <span class="tile tile--light">8</span>
      <span class="tile tile--light pair-break">7</span>
      <span class="tile tile--light">9</span>
    </div>
  </section>

  <section class="stat stat--live">
    <span class="stat-label">Of Live Learners</span>
    <div class="board">
      <span class="tile tile--dark">2</span>
      <span class="tile tile--dark">3</span>
      <span class="tile tile--light pair-break">1</span>
      <span class="tile tile--light">2</span>
    </div>
  </section>

  <section class="stat stat--views">
    <span class="stat-label">Of Total On-Demand Views</span>
    <div class="board board--wide">
      <span class="tile tile--dark">1</span>
      <span class="tile tile--dark">2</span>
      <span class="tile tile--dark pair-break">0</span>
      <span class="tile tile--dark">9</span>
      <span class="tile tile--dark">9</span>
      <span class="tile tile--dark">8</span>
      <span class="tile tile--dark">7</span>
      <span class="tile tile--dark"></span>
      <span class="tile tile--dark"></span>
    </div>
  </section>
</body>
</html>
```